Stationary and email footer design using existing Logo design

Using the Logo design I currently have I need now to have this applied to all stationary requirements including email footer, Letter Head and footer, envelopes both window and non window ( standard letter size ).
You previously did the Logo and business cards so that's good.

```html
<!DOCTYPE html>
<html lang="en">
<head>
<meta charset="utf-8">
<title>Halden &amp; Rowe Advisory – Envelope Stationery</title>
<link rel="stylesheet" href="https://fonts.googleapis.com/css2?family=Open+Sans:wght@700&display=swap">
<style>
  :root {
    --backdrop: #9f9f9f;
    --paper: #f4f4f4;
    --brand-purple: #9b79c4;
    --flap-purple: #a588cc;
    --band-grey: #a9a9ab;
    --crease: #dcdcde;
  }
  * { margin: 0; padding: 0; box-sizing: border-box; }
  html, body {
    width: 1200px;
    height: 950px;
    overflow: hidden;
    background: var(--backdrop);
  }
  .sheet {
    position: relative;
    width: 1200px;
    height: 950px;
  }
  .envelope {
    position: absolute;
    left: 170px;
    width: 860px;
    height: 430px;
    background: var(--paper);
    box-shadow: 0 6px 14px rgba(0,0,0,0.18);
    overflow: hidden;
  }
  .envelope--front { top: 30px; }
  .envelope--back  { top: 490px; }
  .envelope svg.art {
    position: absolute;
    inset: 0;
    width: 100%;
    height: 100%;
  }
  .sender {
    position: absolute;
    left: 52px;
    top: 48px;
    color: var(--brand-purple);
    font-family: "Open Sans", sans-serif;
    font-weight: 700;
  }
  .sender__mark {
    display: flex;
    align-items: center;
    gap: 10px;
  }
  .sender__square {
    width: 24px;
    height: 24px;
    background: var(--brand-purple);
  }
  .sender__name {
    font-size: 22px;
    line-height: 1.2;
  }
  .sender__address {
    margin-top: 10px;
    font-size: 11px;
    line-height: 1.45;
  }
  .back-mark {
    position: absolute;
    right: 150px;
    bottom: 70px;
    display: flex;
    align-items: center;
    gap: 8px;
    color: var(--brand-purple);
    font-family: "Open Sans", sans-serif;
    font-weight: 700;
    font-size: 14px;
  }
  .back-mark__square {
    width: 18px;
    height: 18px;
    background: var(--brand-purple);
  }
</style>
</head>
<body>
<main class="sheet">

  <section class="envelope envelope--front" aria-label="Envelope front">
    <svg class="art" viewBox="0 0 860 430" aria-hidden="true">
      <path class="band-grey" fill="var(--band-grey)"
            d="M0,430 L0,400 C260,392 600,330 860,150 L860,430 Z"/>
      <path class="swoosh-white" fill="var(--paper)"
            d="M0,402 C260,378 610,300 860,140 L860,160 C610,318 260,392 0,408 Z"/>
      <path class="swoosh-purple" fill="var(--brand-purple)"
            d="M180,378 C420,330 660,250 860,120 L860,134 C650,270 420,345 180,378 Z"/>
    </svg>
    <div class="sender">
      <div class="sender__mark">
        <span class="sender__square"></span>
        <span class="sender__name">Halden &amp; Rowe<br>Advisory</span>
      </div>
      <p class="sender__address">Suite 4, Level 2 Harbour Court 15 Wattle Lane,<br>Marlow WA 6110</p>
    </div>
  </section>

  <section class="envelope envelope--back" aria-label="Envelope back">
    <svg class="art" viewBox="0 0 860 430" aria-hidden="true">
      <path class="pocket-crease" fill="none" stroke="var(--crease)" stroke-width="2"
            d="M40,430 L40,215 Q40,170 90,165 L770,150 Q815,148 820,195 L820,430"/>
    </svg>
    <svg class="art" viewBox="0 0 860 430">
      <path class="flap" role="img" aria-label="Flap lining with purple geometric pattern"
            fill="var(--flap-purple)"
            d="M0,0 L860,0 L860,40 Q860,70 820,80 L120,160 Q40,168 18,150 Q0,138 0,110 Z"/>
    </svg>
    <div class="back-mark">
      <span class="back-mark__square"></span>
      <span>Halden &amp; Rowe</span>
    </div>
  </section>

</main>
</body>
</html>
```